Bramblewood Card Company Business Cards

We are a trading card store with Glimmorax, sports and other TCG cards, we need a business card design that encompasses a clean cut, modern style with a retro flare. website is bramblewoodcardco.com for reference. Can utilize a comic book era feel or a more modern outdoor feel to utilize the "Pacific Northwest" elements of tress, mountains, etc.

Industry/Entity Type

Trading cards and collectibles

Contact Information for Business Card

business name, email address, phone number, name, owner job title

Font styles to use
Sans Serif

```html
<!DOCTYPE html>
<html lang="en">
<head>
<meta charset="utf-8">
<title>Bramblewood Card Company – Business Cards</title>
<link href="https://fonts.googleapis.com/css2?family=Montserrat:wght@700;800&family=Josefin+Sans:wght@400;600&display=swap" rel="stylesheet">
<style>
  :root {
    --backdrop: #4a3223;
    --card-grey: #767676;
    --frame-white: #ffffff;
    --sky-blue: #20bfe0;
    --ink-grey: #6f6f6f;
    --text-white: #ffffff;
  }
  * { box-sizing: border-box; margin: 0; padding: 0; }
  html, body { width: 1200px; height: 1200px; overflow: hidden; }
  body { background: var(--backdrop); font-family: "Josefin Sans", sans-serif; }
  .stage { position: relative; width: 1200px; height: 1200px; }

  .card {
    position: absolute;
    width: 454px;
    height: 756px;
    background: var(--card-grey);
  }
  .card--front { left: 117px; top: 222px; }
  .card--back  { left: 628px; top: 221px; }

  .card__panel {
    position: absolute;
    left: 36px; top: 33px;
    width: 384px; height: 686px;
    border: 9px solid var(--frame-white);
    border-radius: 14px;
    background: var(--sky-blue);
    overflow: hidden;
  }

  .brand-mark {
    position: absolute;
    left: 0; right: 0;
    text-align: center;
    font-family: "Montserrat", sans-serif;
    font-weight: 800;
    color: var(--ink-grey);
    letter-spacing: 1px;
    line-height: 1.1;
  }
  .card--front .brand-mark { top: 92px; font-size: 24px; }
  .card--back .brand-mark { top: 270px; font-size: 34px; }
  .brand-mark__dot {
    display: block;
    width: 46px; height: 46px;
    margin: 0 auto 12px;
    border-radius: 50%;
    background: var(--ink-grey);
  }
  .card--back .brand-mark__dot { width: 64px; height: 64px; margin-bottom: 16px; }

  .headline {
    position: absolute;
    left: 0; right: 0; top: 254px;
    text-align: center;
    font-family: "Montserrat", sans-serif;
    font-weight: 800;
    font-size: 33px;
    line-height: 39px;
    color: var(--text-white);
  }

  .person-name {
    position: absolute;
    left: 0; right: 0; top: 378px;
    text-align: center;
    font-size: 31px;
    color: var(--text-white);
  }

  .job-ribbon { position: absolute; left: 85px; top: 416px; width: 178px; height: 40px; }
  .job-ribbon__label {
    position: absolute; left: 0; right: 0; top: 424px;
    text-align: center;
    font-size: 23px;
    color: var(--text-white);
  }

  .contact-divider { position: absolute; left: 62px; width: 224px; height: 30px; }
  .contact-divider--phone { top: 478px; }
  .contact-divider--mail  { top: 565px; }

  .contact-text {
    position: absolute; left: 0; right: 0;
    text-align: center;
    color: var(--text-white);
  }
  .contact-text--phone { top: 519px; font-size: 23px; }
  .contact-text--mail  { top: 604px; font-size: 21px; letter-spacing: 0.5px; }

  .mountain-band {
    position: absolute;
    left: 0; right: 0; bottom: 0;
    height: 120px;
    background: linear-gradient(to bottom, rgba(118,118,118,0) 0%, var(--card-grey) 55%, var(--card-grey) 100%);
  }
</style>
</head>
<body>
<main class="stage">

  <section class="card card--front" aria-label="Business card front">
    <div class="card__panel">
      <div class="brand-mark"><span class="brand-mark__dot"></span>BRAMBLEWOOD<br>CARD COMPANY</div>

      <h1 class="headline">BRAMBLEWOOD<br>CARD COMPANY</h1>

      <p class="person-name">Your Name</p>

      <svg class="job-ribbon" viewBox="0 0 178 40" aria-hidden="true">
        <polygon points="0,6 36,6 36,40 0,40 10,23" fill="var(--ink-grey)"/>
        <polygon points="178,6 142,6 142,40 178,40 168,23" fill="var(--ink-grey)"/>
        <rect x="20" y="0" width="138" height="36" fill="var(--ink-grey)" stroke="var(--sky-blue)" stroke-width="2"/>
      </svg>
      <p class="job-ribbon__label">Job Title</p>

      <svg class="contact-divider contact-divider--phone" viewBox="0 0 224 30" aria-hidden="true">
        <g fill="var(--text-white)">
          <rect x="0" y="11" width="89" height="3"/><rect x="0" y="17" width="89" height="3"/>
          <rect x="135" y="11" width="89" height="3"/><rect x="135" y="17" width="89" height="3"/>
        </g>
        <polygon points="112,1 125,8 125,23 112,30 99,23 99,8" fill="var(--ink-grey)"/>
        <path d="M106 9 q2 -1 3 1 l1 3 q0 1 -1 2 q1 3 4 4 q1 -1 2 -1 l3 1 q2 1 1 3 q-2 2 -5 1 q-7 -3 -9 -9 q-1 -3 1 -5z" fill="var(--text-white)"/>
      </svg>
      <p class="contact-text contact-text--phone">123 123 123</p>

      <svg class="contact-divider contact-divider--mail" viewBox="0 0 224 30" aria-hidden="true">
        <g fill="var(--text-white)">
          <rect x="0" y="11" width="89" height="3"/><rect x="0" y="17" width="89" height="3"/>
          <rect x="135" y="11" width="89" height="3"/><rect x="135" y="17" width="89" height="3"/>
        </g>
        <polygon points="112,1 125,8 125,23 112,30 99,23 99,8" fill="var(--ink-grey)"/>
        <rect x="104" y="10" width="16" height="11" rx="1.5" fill="var(--text-white)"/>
        <polyline points="104,11 112,17 120,11" fill="none" stroke="var(--ink-grey)" stroke-width="1.5"/>
      </svg>
      <p class="contact-text contact-text--mail">name@email.com</p>
    </div>
  </section>

  <section class="card card--back" aria-label="Business card back">
    <div class="card__panel">
      <div class="brand-mark"><span class="brand-mark__dot"></span>BRAMBLEWOOD<br>CARD COMPANY</div>
      <div class="mountain-band" role="img" aria-label="Grey mountain range silhouette along the bottom edge"></div>
    </div>
  </section>

</main>
</body>
</html>
```